Plakat-Design Workshop gegen Prüfungsangst
Zielgruppe
Prüfungsangst überwinden mittels Workshops: 'Selbsthypnose erlernen'
Zielgruppe Studenten
Schweißausbrüche, Blackout, und Resignation.
Viele kennen diese unangenehmen Momente, wenn eine Prüfung begonnen hat und die Aufgabenstellungen scheinbar unlösbar sind.
Dann ist Entspannung nahezu unmöglich. Das Stresshormon Cortisol wurde bereits ausgeschüttet. Es beeinträchtigt die Erinnerung an das Gelernte.
Die mentale Vorbereitung sollte schon viel eher ansetzen, wenn es noch nicht zu spät ist. Wenn der Körper noch nicht verkrampft ist.
Selbsthypnose vor Prüfungen ist hier eine tolle Möglichkeit.
Mit Hilfe einer geführten Selbsthypnoseanleitung ist es Dir möglich Dein Unterbewusstsein so zu programmieren, dass diese Übererregungszustände vor Prüfungssituationen deutlich reduziert werden.
Aufgabenstellung
DINA 4 Plakat, 'Prüfungsangst?' mit einem Freifeld, wo man Ort, Datum und Zeit der Veranstaltung 'Selbsthypnose erlernen'
(Selbstsicher in die Prüfung) eindrucken kann.
darunter:
Anmeldung: Tel: 01563 8074215
Dipl. Sportl. Henrik Wolde Mentaltraining
weitere Infos auch über Einzelsitzungen: www.wolde-trancepraxis.de

```html
<!DOCTYPE html>
<html lang="de">
<head>
<meta charset="utf-8">
<title>Prüfungsangst? – Workshop Selbsthypnose</title>
<link href="https://fonts.googleapis.com/css2?family=Hind:wght@400;500;600;700&display=swap" rel="stylesheet">
<style>
  :root {
    --red: #e0302a;
    --ink: #111111;
    --rule: #a9a9a9;
    --paper: #ffffff;
    --photo-warm-a: #b86a2c;
    --photo-warm-b: #d99a5a;
    --portrait-a: #8a8a8a;
    --portrait-b: #c9ccd3;
    --badge-ring: #dfe3e6;
    --badge-core: #1d7f8e;
  }
  * { margin: 0; padding: 0; box-sizing: border-box; }
  html, body { width: 881px; height: 1200px; overflow: hidden; background: var(--paper); }
  body { font-family: "Hind", Arial, sans-serif; color: var(--ink); }

  .poster { position: relative; width: 881px; height: 1200px; background: var(--paper); overflow: hidden; }

  .hero-photo {
    position: absolute; left: 0; top: 0; width: 881px; height: 231px;
    background: linear-gradient(90deg, var(--photo-warm-a) 0%, var(--photo-warm-b) 45%, var(--photo-warm-a) 100%);
  }
  .hero-rule { position: absolute; left: 0; top: 235px; width: 881px; height: 7px; background: var(--red); }

  .headline {
    position: absolute; left: 28px; top: 308px;
    font-size: 120px; font-weight: 600; line-height: 1; letter-spacing: -1.5px; color: var(--red);
    white-space: nowrap;
  }
  .symptoms {
    position: absolute; left: 31px; top: 438px;
    font-size: 38px; font-weight: 700; line-height: 1; letter-spacing: -0.3px; white-space: nowrap;
  }
  .intro {
    position: absolute; left: 31px; top: 490px; width: 840px;
    font-size: 29.5px; font-weight: 400; line-height: 37px;
  }
  .claim {
    position: absolute; left: 31px; top: 722px;
    font-size: 69px; font-weight: 600; line-height: 1; letter-spacing: -0.6px; color: var(--red);
    white-space: nowrap;
  }

  .trainer-photo {
    position: absolute; left: 33px; top: 810px; width: 246px; height: 340px;
    background: linear-gradient(160deg, var(--portrait-b) 0%, var(--portrait-a) 100%);
  }
  .badge { position: absolute; left: 222px; top: 1026px; width: 166px; height: 166px; }

  .event-fields { position: absolute; left: 406px; top: 808px; width: 442px; }
  .field { display: flex; align-items: flex-end; height: 42px; margin-bottom: 26px; font-size: 47px; line-height: 1; }
  .field-line { flex: 1; margin-left: 4px; border-bottom: 2px solid var(--rule); margin-bottom: 7px; }

  .registration {
    position: absolute; left: 406px; top: 1012px;
    font-size: 25px; line-height: 28px; font-weight: 400; font-style: normal; white-space: nowrap;
  }
  .registration strong { font-weight: 700; }

  .footer-band { position: absolute; left: 0; top: 1160px; width: 881px; height: 40px; background: var(--red); }
</style>
</head>
<body>
<main class="poster">
  <div class="hero-photo" role="img" aria-label="Foto: gestresste Studentin hält sich in einem Prüfungssaal den Kopf, im Hintergrund weitere Prüflinge"></div>
  <div class="hero-rule"></div>

  <h1 class="headline">Prüfungsangst?</h1>
  <h2 class="symptoms">Schweißausbrüche, Blackout &amp; Resignation?</h2>
  <p class="intro">Im Workshop "Selbsthypnose" lernst Du Strategien, solche<br>Übererregungszustände vor Prüfungen deutlich zu reduzieren.</p>

  <h2 class="claim">Selbstsicher in die Prüfung!</h2>

  <div class="trainer-photo" role="img" aria-label="Porträtfoto des Mentaltrainers vor einer Betonwand"></div>
  <div class="footer-band"></div>
  <svg class="badge" viewBox="0 0 166 166" role="img" aria-label="Zertifizierungssiegel">
    <circle cx="83" cy="83" r="82" fill="#ffffff"/>
    <circle cx="83" cy="83" r="72" fill="var(--badge-ring)" stroke="var(--badge-core)" stroke-width="2"/>
    <circle cx="83" cy="83" r="40" fill="var(--badge-core)"/>
  </svg>

  <section class="event-fields">
    <div class="field"><span>Ort:</span><span class="field-line"></span></div>
    <div class="field"><span>Datum:</span><span class="field-line"></span></div>
    <div class="field"><span>Zeit:</span><span class="field-line"></span></div>
  </section>

  <address class="registration">
    <strong>Anmeldung:</strong><br>
    Tel: 01563 8074215<br>
    Dipl. Sportl. Henrik Wolde Mentaltraining<br>
    weitere Infos auch über Einzelsitzungen:<br>
    <strong>www.wolde-trancepraxis.de</strong>
  </address>
</main>
</body>
</html>
```